Carpet cleaning company focused on high quality needs business cards

We are a growing company that just merged with another company and need to design a new business card. We do both residential as well as commercial cleaning. We do carpet, tile & grout, upholstery, hard floors, and stain & pet odor removal. We treat our customers like family and strive to achieve outstanding results with every job.

```html
<!DOCTYPE html>
<html lang="en">
<head>
<meta charset="utf-8">
<title>Brightwell Carpet Care – Business Cards</title>
<link rel="stylesheet" href="https://fonts.googleapis.com/css2?family=Open+Sans:wght@400;700&display=swap">
<style>
  :root {
    --bg: #2a2a2c;
    --card: #ffffff;
    --red: #ef473d;
    --blue: #0a7cc4;
    --ink: #1a1a1a;
  }
  * { box-sizing: border-box; margin: 0; padding: 0; }
  html, body { width: 1200px; height: 780px; overflow: hidden; }
  body {
    background: var(--bg);
    font-family: "Open Sans", Arial, sans-serif;
    color: var(--ink);
    display: flex;
    align-items: center;
    justify-content: center;
    gap: 48px;
  }
  .card {
    position: relative;
    width: 540px;
    height: 309px;
    background: var(--card);
    border-radius: 26px;
    overflow: hidden;
  }
  .card-wave { position: absolute; inset: 0; width: 100%; height: 100%; }
  .brand {
    position: absolute;
    display: flex;
    align-items: center;
    gap: 16px;
  }
  .brand-square { background: var(--red); flex: none; }
  .brand-name {
    font-weight: 700;
    color: var(--ink);
    line-height: 1.2;
  }
  .card-front .brand { left: 70px; top: 74px; }
  .card-front .brand-square { width: 56px; height: 56px; }
  .card-front .brand-name { font-size: 32px; }

  .card-back .brand { left: 34px; top: 58px; flex-direction: column; align-items: flex-start; gap: 12px; }
  .card-back .brand-square { width: 44px; height: 44px; }
  .card-back .brand-name { font-size: 19px; max-width: 180px; }

  .divider {
    position: absolute;
    left: 232px; top: 44px;
    width: 2px; height: 170px;
    background: var(--blue);
  }
  .contact { position: absolute; left: 254px; top: 48px; }
  .contact-name { font-size: 24px; font-weight: 700; line-height: 1.1; }
  .contact-name .first { color: var(--blue); }
  .contact-name .last { color: var(--red); }
  .contact-role { font-size: 13px; margin-bottom: 10px; }
  .contact-list { list-style: none; font-size: 13.5px; line-height: 1.6; }
  .contact-list li { display: flex; align-items: center; gap: 7px; }
  .contact-list svg { width: 12px; height: 12px; fill: var(--blue); flex: none; }
  .contact-address { font-size: 13.5px; line-height: 1.5; margin-top: 4px; }
</style>
</head>
<body>

<section class="card card-front" aria-label="Business card front">
  <svg class="card-wave" viewBox="0 0 540 309" aria-hidden="true">
    <path d="M0,196 C140,282 330,300 540,238 L540,309 L0,309 Z" fill="var(--red)"/>
    <path d="M0,180 C140,266 330,284 540,222" fill="none" stroke="var(--blue)" stroke-width="4"/>
  </svg>
  <div class="brand">
    <span class="brand-square"></span>
    <span class="brand-name">Brightwell<br>Carpet Care</span>
  </div>
</section>

<section class="card card-back" aria-label="Business card back">
  <svg class="card-wave" viewBox="0 0 540 309" aria-hidden="true">
    <path d="M0,196 C140,282 330,300 540,238 L540,309 L0,309 Z" fill="var(--red)"/>
    <path d="M0,180 C140,266 330,284 540,222" fill="none" stroke="var(--blue)" stroke-width="4"/>
  </svg>
  <div class="brand">
    <span class="brand-square"></span>
    <span class="brand-name">Brightwell<br>Carpet Care</span>
  </div>
  <span class="divider"></span>
  <div class="contact">
    <p class="contact-name"><span class="first">Lena</span> <span class="last">Marsh</span></p>
    <p class="contact-role">Executive Director</p>
    <ul class="contact-list">
      <li><svg viewBox="0 0 24 24"><path d="M6.6 10.8a15.1 15.1 0 0 0 6.6 6.6l2.2-2.2c.3-.3.7-.4 1-.2 1.1.4 2.3.6 3.6.6.6 0 1 .4 1 1V20c0 .6-.4 1-1 1A17 17 0 0 1 3 4c0-.6.4-1 1-1h3.5c.6 0 1 .4 1 1 0 1.3.2 2.5.6 3.6.1.3 0 .7-.2 1z"/></svg>555 010 2468</li>
      <li><svg viewBox="0 0 24 24"><path d="M2 5h20v14H2z M2 5l10 8 10-8"/></svg>info@brightwellcare.com</li>
      <li><svg viewBox="0 0 24 24"><circle cx="12" cy="12" r="10"/></svg>www.brightwellcare.com</li>
    </ul>
    <p class="contact-address">2270 Harbor Way<br>Lake Orin,</p>
  </div>
</section>

</body>
</html>
```